Business Card Design

We are a manufacturing and distribution company with most of our customer base being supermarkets. We have established brand guidelines that are attached.

```html
<!DOCTYPE html>
<html lang="en">
<head>
<meta charset="utf-8">
<title>Velmora Business Card</title>
<link href="https://fonts.googleapis.com/css2?family=Archivo:wght@400;800&display=swap" rel="stylesheet">
<style>
  :root {
    --stage: #2b2b2d;
    --card-white: #ffffff;
    --brand-blue: #0a69ae;
    --brand-red: #e0242b;
    --ink: #1c1c1e;
    --rule: #333333;
    --on-blue: #ffffff;
  }
  html, body {
    margin: 0;
    padding: 0;
    width: 1200px;
    height: 1015px;
    overflow: hidden;
    background: var(--stage);
    font-family: "Archivo", Arial, sans-serif;
  }
  .stage {
    position: relative;
    width: 1200px;
    height: 1015px;
  }
  .card {
    position: absolute;
    left: 320px;
    width: 560px;
    height: 320px;
    box-sizing: border-box;
    box-shadow: 0 12px 30px rgba(0,0,0,0.5);
  }
  /* Front face */
  .card-front {
    top: 150px;
    background: var(--card-white);
  }
  .brand {
    position: absolute;
    left: 0;
    right: 0;
    top: 100px;
    display: flex;
    justify-content: center;
    align-items: center;
    gap: 14px;
  }
  .brand-mark {
    width: 26px;
    height: 26px;
    background: var(--brand-blue);
  }
  .brand-name {
    font-weight: 800;
    font-size: 52px;
    letter-spacing: 3px;
    color: var(--ink);
    line-height: 1;
  }
  .front-web-row {
    position: absolute;
    left: 0;
    right: 24px;
    top: 186px;
    display: flex;
    align-items: center;
    gap: 12px;
    font-size: 15px;
    letter-spacing: 0.5px;
  }
  .front-web {
    margin-left: 196px;
    white-space: nowrap;
  }
  .front-web .accent { color: var(--brand-red); }
  .front-web .domain { color: var(--brand-blue); }
  .front-rule-top {
    flex: 1;
    height: 1px;
    background: var(--rule);
  }
  .front-rule-bottom {
    position: absolute;
    top: 270px;
    left: 40px;
    width: 230px;
    height: 1px;
    background: var(--rule);
  }
  /* Back face */
  .card-back {
    top: 530px;
    background: var(--brand-blue);
    color: var(--on-blue);
    overflow: hidden;
  }
  .holder {
    position: absolute;
    left: 40px;
    top: 68px;
  }
  .holder-name {
    font-weight: 800;
    font-size: 22px;
    letter-spacing: 0.5px;
    margin: 0;
    line-height: 1.1;
  }
  .holder-title {
    font-size: 13px;
    letter-spacing: 0.5px;
    margin: 2px 0 0;
  }
  .contact-list {
    position: absolute;
    left: 40px;
    top: 148px;
    margin: 0;
    padding: 0;
    list-style: none;
    font-size: 15px;
  }
  .contact-list li {
    display: flex;
    align-items: center;
    gap: 8px;
    margin-bottom: 4px;
  }
  .contact-list svg {
    width: 14px;
    height: 14px;
    fill: none;
    stroke: var(--on-blue);
    stroke-width: 1.8;
  }
  .address {
    position: absolute;
    left: 62px;
    top: 250px;
    font-size: 15px;
    font-style: normal;
    line-height: 1.3;
  }
</style>
</head>
<body>
<main class="stage">
  <section class="card card-front" aria-label="Card front">
    <div class="brand">
      <span class="brand-mark" aria-hidden="true"></span>
      <span class="brand-name">VELMORA</span>
    </div>
    <div class="front-web-row">
      <div class="front-web"><span class="accent">www.</span><span class="domain">velmorafoods</span><span class="accent">.com</span></div>
      <div class="front-rule-top"></div>
    </div>
    <div class="front-rule-bottom"></div>
  </section>

  <section class="card card-back" aria-label="Card back">
    <div class="holder">
      <p class="holder-name">DANIEL HARPER</p>
      <p class="holder-title">MANAGING DIRECTOR</p>
    </div>
    <ul class="contact-list">
      <li>
        <svg viewBox="0 0 16 16" aria-hidden="true"><path d="M3 2l3 1 1 3-2 1c1 2 2 3 4 4l1-2 3 1 1 3c-1 1-2 1-3 1C6 14 2 10 2 5c0-1 0-2 1-3z"/></svg>
        044-987 654 321
      </li>
      <li>
        <svg viewBox="0 0 16 16" aria-hidden="true"><rect x="1.5" y="3.5" width="13" height="9"/><path d="M1.5 3.5l6.5 5 6.5-5"/></svg>
        info@velmorafoods.com
      </li>
      <li>
        <svg viewBox="0 0 16 16" aria-hidden="true"><circle cx="8" cy="8" r="6.5"/><ellipse cx="8" cy="8" rx="3" ry="6.5"/><path d="M1.5 8h13"/></svg>
        www.velmorafoods.com
      </li>
    </ul>
    <address class="address">88, Larkfield Road, Unit 5<br>30718, Westmere</address>
  </section>
</main>
</body>
</html>
```